Career Development Skills | Business Card & Logo Design

We are looking for a business card including logo design for a new Sydney based business called 'Bright Pathwork'.
We offer a range of services that focus on building the Employability or Employment skills for individuals focusing on job seekers and those interested in building skills required to develop their career. Employability skills are required not only to gain employment, but also to progress within an organisation so as to achieve one's potential.
Updates
Target Market(s)
Our client targets include corporates and govt agencies looking to build skills within their current employee base or assist staff in the transition between roles or workplaces.
Industry/Entity Type
Business
Look and feel
Each slider illustrates characteristics of the customer's brand and the style your logo design should communicate.

```html
<!DOCTYPE html>
<html lang="en">
<head>
<meta charset="utf-8">
<title>Bright Pathwork – Business Card</title>
<link href="https://fonts.googleapis.com/css2?family=Cinzel:wght@700&family=Pathway+Gothic+One&display=swap" rel="stylesheet">
<style>
  :root {
    --backdrop: #1c1c1c;
    --card-dark-top: #2e2e2e;
    --card-dark-bottom: #141414;
    --card-light-top: #d9d9d9;
    --card-light-bottom: #f4f2f3;
    --teal: #16a3a6;
    --silver: #b9b9b9;
    --ink-grey: #6f6f6f;
  }
  * { margin: 0; padding: 0; box-sizing: border-box; }
  html, body {
    width: 1200px; height: 1164px; overflow: hidden;
    background: var(--backdrop);
  }
  .canvas { position: relative; width: 1200px; height: 1164px; }

  .card { position: absolute; overflow: hidden; box-shadow: 0 6px 18px rgba(0,0,0,.6); }

  /* Front */
  .card-front {
    left: 64px; top: 97px; width: 741px; height: 453px;
    background: linear-gradient(160deg, var(--card-dark-top), var(--card-dark-bottom));
  }
  .brand-mark {
    position: absolute; left: 0; right: 0; top: 150px;
    display: flex; justify-content: center; align-items: center; gap: 12px;
    font-family: "Pathway Gothic One", sans-serif; font-size: 40px; line-height: 1;
    color: var(--silver); letter-spacing: 1px;
  }
  .brand-mark .dot {
    width: 20px; height: 20px; border-radius: 50%; background: var(--teal);
  }
  .front-rule {
    position: absolute; left: 163px; width: 431px; top: 266px; height: 1px;
    background: linear-gradient(90deg, transparent, #9a9a9a 30%, #9a9a9a 70%, transparent);
  }
  .front-title {
    position: absolute; left: 0; right: 0; top: 280px; text-align: center;
    font-family: "Cinzel", serif; font-weight: 700; font-size: 30px; line-height: 1;
    color: var(--teal); letter-spacing: 2px;
  }

  /* Back */
  .card-back {
    left: 388px; top: 586px; width: 740px; height: 452px;
    background: linear-gradient(135deg, var(--card-light-top), var(--card-light-bottom));
    font-family: "Pathway Gothic One", sans-serif; font-size: 18px; line-height: 1;
  }
  .back-rule {
    position: absolute; left: 165px; top: 104px; width: 2px; height: 253px;
    background: var(--teal);
  }
  .contact, .address, .numbers { position: absolute; left: 192px; }
  .contact { top: 102px; color: var(--teal); }
  .contact p { height: 21px; }
  .address { top: 192px; color: var(--ink-grey); }
  .address p { height: 23px; }
  .numbers { top: 316px; }
  .numbers p { height: 25px; }
  .numbers .label { color: var(--teal); }
  .numbers .value { color: var(--ink-grey); }
</style>
</head>
<body>
<div class="canvas">
  <section class="card card-front">
    <div class="brand-mark"><span class="dot"></span><span>Bright Pathwork</span></div>
    <div class="front-rule"></div>
    <h1 class="front-title">BRIGHT PATHWORK</h1>
  </section>

  <section class="card card-back">
    <div class="back-rule"></div>
    <div class="contact">
      <p>Daniel Reeve - Director</p>
      <p>Brightpathwork.com.au</p>
      <p>Daniel@brightpathwork.com.au</p>
    </div>
    <div class="address">
      <p>Level 14</p>
      <p>Harbour View Tower 3</p>
      <p>118&nbsp;&nbsp;&nbsp; Kent Lane</p>
      <p>Harbour Park, Sydney 2000</p>
    </div>
    <div class="numbers">
      <p><span class="label">Tell ----------------</span><span class="value">(02)&nbsp; 95550130</span></p>
      <p><span class="label">Fax ----------------</span><span class="value"> (02)&nbsp; 95550110</span></p>
    </div>
  </section>
</div>
</body>
</html>
```